Brimora - Nutritious Snacks and Desserts

We need a creative e-commerce website in which all features--buttons, background, etc.--convey our message: We sell delicious, nutritious snacks and desserts that most closely comply with the paleo diet guidelines. Our first product is Nuttaree®--raw, vegan, paleo chocolate balls that are made of dates, coconut, and cocoa. Our products are organic, raw, irresistible and nutritious. We have several versions of Nuttaree® in development, as well as mousse, ice cream, and crackers. Our mission is to purvey basic healthy foods. Our motto is, "Fuel for the Bold Trail-Walker(tm)."

Target Market(s)

Health-conscious professionals who tend to shop at health food stores. Our products also meet the requirements of a gluten-free diet; and they also don't contain refined sugar, so shoppers with gluten and possibly sugar issues are incidental customers.

Industry/Entity Type

Health Product

Coding

Number of Pages Required

5+ page

Colors

Designer to choose colors to be used in the design.

Requirements
Must have
• We need at least a home page, a products page, an about-us page, a contact page, and a shopping cart page. We would like to be able to add products on our own later. We should be able to handle some basic coding, especially if it's just a matter of copying and modifying product pages. We would also like the ability in the future to add blogging pages, allowing us to write articles about health food and healthy lifestyle, thus attracting web-traffic (SEO).
• Other features we would like to have:
• Product photo slider on the hopepage
• Back-to-top button at the bottom of the home page
• Make sure the site is mobile-compatible
• A search bar at the top of the homepage
• "Create an account" and "Previous orders"--allowing customers to see their previous orders and reorder what they purchased in the past.
Nice to have
• We would like to convey the paleo theme without actually stating it anywhere. We'll add text as necessary, according to the page layout; you can use ipsum lorem for purpose of demonstration.

```html
<!DOCTYPE html>
<html lang="en">
<head>
<meta charset="utf-8">
<title>Brimora – Nutritious Snacks and Desserts</title>
<link rel="stylesheet" href="https://fonts.googleapis.com/css2?family=Montserrat:wght@400;500;600;700&family=Open+Sans:wght@400;600;700&family=Raleway:wght@300;400;500&display=swap">
<style>
:root{
  --green:#6cc417;
  --green-dark:#5aab0f;
  --ink:#222;
  --text:#333;
  --muted:#777;
  --line:#e3e3e3;
  --soft-bg:#f2f2f2;
  --footer-bg:#333333;
  --footer-text:#d6d6d6;
  --footer-line:#4d4d4d;
}
*{box-sizing:border-box;margin:0;padding:0}
html,body{width:787px;height:1200px;overflow:hidden;background:#fff}
body{font-family:"Open Sans",Arial,sans-serif;color:var(--text)}
.page{position:relative;width:787px;height:1200px;overflow:hidden}
.abs{position:absolute}

/* header */
.top-rule{left:0;top:0;width:787px;height:3px;background:var(--green)}
.header{left:0;top:3px;width:787px;height:83px;background:#fff}
.brand{left:104px;top:12px;display:flex;flex-direction:column;align-items:center;gap:6px}
.brand-dot{width:38px;height:38px;border-radius:50%;background:var(--green)}
.brand-name{font-family:"Montserrat",sans-serif;font-weight:600;font-size:17px;color:var(--green);letter-spacing:1px}
.search{left:421px;top:19px;width:178px;height:26px;border:1px solid #cfcfcf;display:flex}
.search-field{flex:1;font-family:"Open Sans",sans-serif;font-style:italic;font-size:7px;color:#555;padding:0 6px;display:flex;align-items:center}
.search-btn{width:30px;border-left:1px solid #cfcfcf;display:flex;align-items:center;justify-content:center}
.basket{left:608px;top:18px;display:flex;align-items:center;gap:5px}
.basket-title{font-family:"Montserrat",sans-serif;font-weight:700;font-size:12px;color:var(--green);line-height:1}
.basket-count{font-size:7px;color:#333;margin-top:2px}
.nav{left:0;top:63px;width:787px;font-family:"Montserrat",sans-serif;font-weight:600;font-size:8px;color:var(--ink)}
.nav a{position:absolute;text-decoration:none;color:inherit;white-space:nowrap}
.nav a.active{color:var(--green)}

/* hero */
.hero{left:0;top:86px;width:787px;height:324px;background:linear-gradient(90deg,#8a7062 0%,#6f4b36 35%,#a0785a 60%,#6a3f27 100%)}
.hero-shade{left:0;top:86px;width:787px;height:324px;background:linear-gradient(180deg,rgba(200,200,200,.35) 0%,rgba(0,0,0,0) 40%,rgba(40,20,10,.25) 100%)}
.hero-title{left:105px;top:179px;font-family:"Montserrat",sans-serif;font-weight:700;font-size:25px;line-height:29px;color:#fff}
.hero-title sup{font-size:9px;vertical-align:top;position:relative;top:3px}
.btn-green{background:var(--green);color:#fff;font-family:"Montserrat",sans-serif;font-weight:500;border-radius:20px;display:flex;align-items:center;justify-content:center}
.hero-btn{left:105px;top:278px;width:108px;height:30px;font-size:8.5px;box-shadow:0 2px 3px rgba(0,0,0,.25)}
.slider-arrow{top:224px;width:22px;height:22px;border:1px solid #fff;border-radius:50%;display:flex;align-items:center;justify-content:center}

/* welcome */
.welcome{left:0;top:410px;width:787px;height:148px;background:var(--soft-bg);text-align:center}
.section-title{font-family:"Montserrat",sans-serif;font-weight:600;font-size:16px;color:var(--ink)}
.section-title span{color:var(--green)}
.welcome .section-title{margin-top:25px}
.welcome-copy{font-family:"Montserrat",sans-serif;font-size:8.6px;line-height:14.5px;color:#222;margin-top:14px}
.welcome-tag{font-family:"Montserrat",sans-serif;font-size:13px;color:#111;margin-top:11px}

/* products */
.featured-title{left:0;top:582px;width:787px;text-align:center}
.card{top:623px;width:133px;height:204px;border:1px solid var(--line);background:#fff;text-align:center}
.card-img{width:131px;height:98px}
.card-price{font-family:"Open Sans",sans-serif;font-weight:600;font-size:9.5px;color:var(--green);margin-top:12px}
.card-desc{font-size:6.8px;line-height:12px;color:#444;margin-top:4px}
.stars{margin-top:5px;display:flex;justify-content:center;gap:1px}
.card-btn{margin:9px auto 0;width:69px;height:18px;border-radius:10px;border:1.2px solid #666;font-family:"Montserrat",sans-serif;font-weight:600;font-size:6.4px;color:#555;display:flex;align-items:center;justify-content:center}
.card-btn.primary{background:var(--green);border-color:var(--green);color:#fff}

/* newsletter */
.newsletter{left:0;top:864px;width:787px;height:120px;background:linear-gradient(180deg,#f5f5f5,#eeeeee)}
.news-bowl{left:89px;top:902px;width:116px;height:116px;border-radius:50%;background:radial-gradient(circle at 45% 45%,#c9a06a 0%,#b3773e 45%,#c86a38 70%,#d8b89a 100%)}
.news-title{left:0;top:881px;width:787px;text-align:center;font-family:"Raleway",sans-serif;font-weight:400;font-size:17px;color:#333}
.news-sub{left:0;top:910px;width:787px;text-align:center;font-size:7.5px;color:#444}
.news-form{left:222px;top:934px;width:343px;height:26px;border:1px solid #ddd;border-radius:14px;background:#fff;display:flex;overflow:hidden}
.news-input{flex:1;font-style:italic;font-size:6.5px;color:#777;display:flex;align-items:center;padding-left:10px}
.news-btn{width:51px;height:100%;border-radius:0 14px 14px 0;font-size:7.5px;font-weight:600}

/* footer */
.footer{left:0;top:984px;width:787px;height:216px;background:var(--footer-bg)}
.foot-head{top:1004px;font-family:"Montserrat",sans-serif;font-weight:500;font-size:10.5px;color:#fff}
.foot-rule{left:106px;top:1030px;width:575px;height:1px;background:var(--footer-line)}
.foot-accent{top:1029px;width:14px;height:3px;background:var(--green)}
.foot-list{top:1052px;list-style:none;font-size:7px;line-height:12.3px;color:var(--footer-text)}
.contact-item{display:flex;gap:8px;margin-bottom:6px}
.contact-icon{width:13px;height:13px;border:1px solid #888;border-radius:50%;flex:none;display:flex;align-items:center;justify-content:center}
.foot-bottom-rule{left:106px;top:1155px;width:575px;height:1px;background:var(--footer-line)}
.socials{left:97px;top:1165px;display:flex;gap:4px}
.social-dot{width:18px;height:18px;border-radius:50%;background:#5b5b5b}
.copyright{left:481px;top:1173px;width:200px;text-align:right;font-size:7px;color:var(--footer-text)}
</style>
</head>
<body>
<div class="page">

  <!-- header -->
  <div class="abs top-rule"></div>
  <header class="abs header"></header>
  <div class="abs brand">
    <div class="brand-dot"></div>
    <div class="brand-name">brimora</div>
  </div>
  <div class="abs search">
    <div class="search-field">Enter keyword</div>
    <div class="search-btn">
      <svg width="9" height="9" viewBox="0 0 10 10"><circle cx="4" cy="4" r="3" fill="none" stroke="#333" stroke-width="1.4"/><line x1="6.3" y1="6.3" x2="9" y2="9" stroke="#333" stroke-width="1.6"/></svg>
    </div>
  </div>
  <div class="abs basket">
    <svg width="27" height="26" viewBox="0 0 27 26"><path d="M1 3h4l4 13h14l3-10H7" fill="none" stroke="#6cc417" stroke-width="2.4" stroke-linejoin="round"/><path d="M8 7h17l-2.6 8H10.5z" fill="#6cc417"/><circle cx="11" cy="21.5" r="2.3" fill="#6cc417"/><circle cx="21" cy="21.5" r="2.3" fill="#6cc417"/></svg>
    <div>
      <div class="basket-title">Basket</div>
      <div class="basket-count">(0.00 items)</div>
    </div>
  </div>
  <nav class="abs nav">
    <a class="active" style="left:280px">HOME</a>
    <a style="left:340px">ALL PRODUCTS</a>
    <a style="left:438px">OFFERS</a>
    <a style="left:504px">PALEO DIET</a>
    <a style="left:586px">BLOG</a>
    <a style="left:643px">CONTACT</a>
  </nav>

  <!-- hero slider -->
  <div class="abs hero" role="img" aria-label="Photo of ice cream scoops with caramel sauce in a waffle bowl on a wooden table"></div>
  <div class="abs hero-shade"></div>
  <h1 class="abs hero-title">Fuel<br>for the Bold<br>Trail-Walker<sup>TM</sup></h1>
  <div class="abs btn-green hero-btn">MORE PRODUCTS</div>
  <div class="abs slider-arrow" style="left:23px">
    <svg width="8" height="8" viewBox="0 0 8 8"><path d="M5.5 1 2.5 4l3 3" fill="none" stroke="#fff" stroke-width="1"/></svg>
  </div>
  <div class="abs slider-arrow" style="left:752px">
    <svg width="8" height="8" viewBox="0 0 8 8"><path d="M2.5 1l3 3-3 3" fill="none" stroke="#fff" stroke-width="1"/></svg>
  </div>

  <!-- welcome -->
  <section class="abs welcome">
    <h2 class="section-title">WELCOME TO <span>BRIMORA FOODS.</span></h2>
    <p class="welcome-copy">Our products are raw, organic, vegan, gluten-free, dairy-free, fiber-rich, nutrient-dense, antioxidant-rich<br>real foods with no preservatives, no added sugar, and no artificial or plant-based sweeteners.</p>
    <p class="welcome-tag">And they are irresistibly scrumptious!</p>
  </section>

  <!-- featured products -->
  <h2 class="abs section-title featured-title">FEATURED <span>PRODUCTS</span></h2>

  <article class="abs card" style="left:106px">
    <div class="card-img" role="img" aria-label="Photo of banana pudding in a glass topped with banana slices and mint" style="background:linear-gradient(180deg,#f4f4f0,#e8e4c0 60%,#d9d6cc)"></div>
    <div class="card-price">$ 150.00</div>
    <p class="card-desc">Sed ut perspiciatis unde omniste<br>natus error sit voluptatem acc.</p>
    <div class="stars"><svg width="36" height="6" viewBox="0 0 36 6" fill="#ccc"><circle cx="3" cy="3" r="2.4"/><circle cx="10.5" cy="3" r="2.4"/><circle cx="18" cy="3" r="2.4"/><circle cx="25.5" cy="3" r="2.4"/><circle cx="33" cy="3" r="2.4"/></svg></div>
    <div class="card-btn primary">ADD TO CART</div>
  </article>

  <article class="abs card" style="left:254px">
    <div class="card-img" role="img" aria-label="Photo of chocolate mousse in a glass bowl with chocolate pieces" style="background:linear-gradient(160deg,#d9cfc8,#7a4a33 50%,#a57a62)"></div>
    <div class="card-price">$ 230.00</div>
    <p class="card-desc">Sed ut perspiciatis unde omniste<br>natus error sit voluptatem acc.</p>
    <div class="stars"><svg width="36" height="6" viewBox="0 0 36 6" fill="#ccc"><circle cx="3" cy="3" r="2.4"/><circle cx="10.5" cy="3" r="2.4"/><circle cx="18" cy="3" r="2.4"/><circle cx="25.5" cy="3" r="2.4"/><circle cx="33" cy="3" r="2.4"/></svg></div>
    <div class="card-btn">ADD TO CART</div>
  </article>

  <article class="abs card" style="left:401px">
    <div class="card-img" role="img" aria-label="Photo of a paper tub of chocolate dessert on a wooden table" style="background:linear-gradient(180deg,#6b6b60,#d8d2bf 45%,#8c6a45 80%,#5a4a38)"></div>
    <div class="card-price">$ 250.00</div>
    <p class="card-desc">Sed ut perspiciatis unde omniste<br>natus error sit voluptatem acc.</p>
    <div class="stars"><svg width="36" height="6" viewBox="0 0 36 6" fill="#ccc"><circle cx="3" cy="3" r="2.4"/><circle cx="10.5" cy="3" r="2.4"/><circle cx="18" cy="3" r="2.4"/><circle cx="25.5" cy="3" r="2.4"/><circle cx="33" cy="3" r="2.4"/></svg></div>
    <div class="card-btn">ADD TO CART</div>
  </article>

  <article class="abs card" style="left:549px">
    <div class="card-img" role="img" aria-label="Photo of vanilla and pistachio ice cream scoops in a white bowl" style="background:linear-gradient(170deg,#eef0ea,#dfe4cf 45%,#9fc4bd 85%)"></div>
    <div class="card-price">$ 280.00</div>
    <p class="card-desc">Sed ut perspiciatis unde omniste<br>natus error sit voluptatem acc.</p>
    <div class="stars"><svg width="36" height="6" viewBox="0 0 36 6" fill="#ccc"><circle cx="3" cy="3" r="2.4"/><circle cx="10.5" cy="3" r="2.4"/><circle cx="18" cy="3" r="2.4"/><circle cx="25.5" cy="3" r="2.4"/><circle cx="33" cy="3" r="2.4"/></svg></div>
    <div class="card-btn">ADD TO CART</div>
  </article>

  <!-- newsletter -->
  <section class="abs newsletter"></section>
  <div class="abs news-bowl" role="img" aria-label="Photo of a wooden bowl with fresh fruit, peppers and nuts"></div>
  <h2 class="abs news-title">Newsletter</h2>
  <p class="abs news-sub">Sign up for our mailing list to get latest updates and offers</p>
  <div class="abs news-form">
    <div class="news-input">Email Address:</div>
    <div class="btn-green news-btn">SIGNUP</div>
  </div>

  <!-- footer -->
  <footer class="abs footer"></footer>
  <h3 class="abs foot-head" style="left:106px">Contact</h3>
  <h3 class="abs foot-head" style="left:254px">Information</h3>
  <h3 class="abs foot-head" style="left:386px">Customer Service</h3>
  <h3 class="abs foot-head" style="left:514px">My Account</h3>
  <h3 class="abs foot-head" style="left:631px">Extras</h3>
  <div class="abs foot-rule"></div>
  <div class="abs foot-accent" style="left:106px"></div>
  <div class="abs foot-accent" style="left:254px"></div>
  <div class="abs foot-accent" style="left:386px"></div>
  <div class="abs foot-accent" style="left:514px"></div>
  <div class="abs foot-accent" style="left:631px"></div>

  <ul class="abs foot-list" style="left:106px;top:1054px">
    <li class="contact-item">
      <span class="contact-icon"><svg width="6" height="7" viewBox="0 0 6 7"><path d="M3 6.6S.6 4 .6 2.6a2.4 2.4 0 0 1 4.8 0C5.4 4 3 6.6 3 6.6z" fill="none" stroke="#aaa" stroke-width=".8"/><circle cx="3" cy="2.6" r=".8" fill="#aaa"/></svg></span>
      <span>48 Ridge Lane, Cedar Hollow,<br>Greenfield.</span>
    </li>
    <li class="contact-item">
      <span class="contact-icon"><svg width="7" height="7" viewBox="0 0 7 7"><path d="M1.4.6l1.2 1.5-.7.9a4 4 0 0 0 2.1 2.1l.9-.7 1.5 1.2-.8.9C3 6.3.7 4 .5 1.4z" fill="none" stroke="#aaa" stroke-width=".7"/></svg></span>
      <span>+0412 5587 20<br>+1480 22 7361</span>
    </li>
    <li class="contact-item">
      <span class="contact-icon"><svg width="7" height="5" viewBox="0 0 7 5"><rect x=".4" y=".4" width="6.2" height="4.2" fill="none" stroke="#aaa" stroke-width=".7"/><path d="M.4.5 3.5 3 6.6.5" fill="none" stroke="#aaa" stroke-width=".7"/></svg></span>
      <span>hello@brimora.shop</span>
    </li>
  </ul>
  <ul class="abs foot-list" style="left:255px"><li>About Us</li><li>Delivery Information</li><li>Privacy Policy</li><li>Terms &amp; Conditions</li><li>&nbsp;Blog</li><li>&nbsp;Careers</li></ul>
  <ul class="abs foot-list" style="left:387px"><li>Contact Us</li><li>Returns</li><li>Site Map</li><li>Gift Certificates</li><li>Affiliates</li><li>Specials</li></ul>
  <ul class="abs foot-list" style="left:514px"><li>My Account</li><li>Order History</li><li>Wish List</li><li>Newsletter</li><li>Our Products</li><li>Herbal</li></ul>
  <ul class="abs foot-list" style="left:631px"><li>Gift Certificates</li><li>Affiliates</li><li>Specials</li><li>Wish List</li><li>My Account</li><li>Order History</li></ul>

  <div class="abs foot-bottom-rule"></div>
  <div class="abs socials" aria-label="Social links">
    <span class="social-dot"></span><span class="social-dot"></span><span class="social-dot"></span><span class="social-dot"></span><span class="social-dot"></span><span class="social-dot"></span>
  </div>
  <p class="abs copyright">Copyright © 2018 Brimora.All Rights reserved.</p>

</div>
</body>
</html>
```